Lamp Over The Valleys- a non profit locin TZ , east Africa. Needing to attract donors.

A flyer for donors /potential partners. showing what their giving has accomplished this year. An Encouraging way to say thank you at the same time informing the partner of the amazing things God is doing with their generous, faithful giving. We will need to print/email. Thank you for considering this project. Your efforts help in educating and feeding 225 street children, providing a safe haven and trade school for hundreds of women and abused teenagers, medical ship on the longest lake in the world going into unreached people groups, a Bible College Training up pastors to plant churches all over TZ, Congo, Burundi and beyond, youth and children’s kids clubs and youth camps. These are the main areas of lamp over the valleys. Bible college, primary school, trade schools, youth camps/kids clubs. We need help in making sure readers will be drawn to seeing/reading more which leads to donations without overwhelming with too much info. HELP! I can tell you about Jesus I have even authored 7 books, but making s flyer that makes sense it out of my wheelhouse. Again, thank you.

I do not want longer I need quicker and paid for a 3 day quote. All pictures and logo are on our website. I have tried to send pictures but they won’t send. Please look at. Www.lampoverthevalleystz.example

Target Market(s)

Professional adults, large companies, donors

Industry/Entity Type

Non profit missionary Lamp over the Valleys in Tanzania, Congo, USA and soon to be Canada.

Requirements
Must have
• Color professional pictures, feel good, exciting want to be apart of what God is doing
Nice to have
• Glossy trifold
Should not have
• Fly in the face, guilt feeling, animals in Africa

```html
<!DOCTYPE html>
<html lang="en">
<head>
<meta charset="utf-8">
<title>Lamp over the Valleys – Trifold</title>
<link href="https://fonts.googleapis.com/css2?family=Exo+2:ital,wght@0,300;0,400;0,500;0,600;0,700;0,800;1,700;1,800&display=swap" rel="stylesheet">
<style>
:root{
  --lime:#c9d38f;
  --lime-bright:#d8e39a;
  --charcoal:#3a3a3c;
  --charcoal-deep:#2c2c2e;
  --ink:#2e2e30;
  --paper:#ffffff;
  --stage:#6d6e71;
  --heart:#c8202d;
  --book:#3fc4ef;
  --gold:#b08a4a;
}
*{margin:0;padding:0;box-sizing:border-box}
html,body{width:844px;height:1200px;overflow:hidden;background:var(--stage);font-family:"Exo 2",sans-serif;color:var(--ink)}
.sheet{position:absolute;left:52px;width:740px;height:576px;overflow:hidden;box-shadow:0 6px 12px rgba(0,0,0,.45)}
.sheet--outside{top:14px}
.sheet--inside{top:610px;background:var(--paper)}
.panel{position:absolute;top:0;height:576px}
.abs{position:absolute}

/* outside – left panel */
.panel--ways{left:0;width:247px;background:var(--paper)}
.panel--ways .top-strip{left:0;top:0;width:247px;height:12px;background:var(--charcoal)}
.way-title{position:absolute;font-weight:500;font-size:18px;line-height:1.05;color:var(--ink)}
.way-title b{font-weight:600;font-size:21px;display:block}
.way-text{position:absolute;font-weight:400;font-size:11px;line-height:1.2;color:var(--ink)}
.divider{position:absolute;left:62px;width:150px;height:2px;background:linear-gradient(90deg,transparent,#bbb,transparent)}
.photo-field{left:0;top:466px;width:247px;height:110px;background:linear-gradient(180deg,#f1f1ee 0%,#c9c6ab 35%,#8d8a5e 70%,#6a6642 100%)}

/* outside – middle panel */
.panel--mission{left:247px;width:246px;background:var(--lime)}
.photo-faded{left:0;top:0;width:246px;height:576px;background:radial-gradient(ellipse at 40% 20%,#9ea76b 0%,rgba(180,190,125,.6) 40%,transparent 75%),linear-gradient(180deg,#b5bf7f,#c9d38f 60%,#b8c282)}
.mission-head{left:0;width:246px;top:152px;text-align:center;font-weight:700;font-size:27px;line-height:1.2;color:var(--ink)}
.mission-sub{left:0;width:246px;top:246px;text-align:center;font-weight:600;font-size:19px;line-height:1.17;color:var(--ink)}
.verse{left:0;width:246px;top:333px;text-align:center;font-weight:600;font-size:18px}
.org-name{left:0;width:246px;top:419px;text-align:center;font-weight:600;font-size:20px;color:#3d3d38}
.contact{left:0;width:246px;text-align:center;font-size:11px;font-weight:500;line-height:1.3}

/* outside – cover panel */
.panel--cover{left:493px;width:247px;background:var(--charcoal)}
.org-wordmark{left:0;width:247px;top:36px;text-align:center;font-weight:700;font-size:27px;line-height:1.05;color:var(--lime-bright)}
.thanks{left:17px;top:126px;font-weight:800;font-size:37px;color:var(--lime-bright);line-height:1}
.thanks-sub{left:17px;top:164px;font-weight:700;font-size:16px;line-height:1.2;color:#fff}
.photo-kids{left:0;top:221px;width:247px;height:184px;background:linear-gradient(135deg,#3e4a5c 0%,#5d6b7b 40%,#7b6653 70%,#4b3a30 100%)}
.cover-text{left:16px;width:215px;top:424px;text-align:center;font-size:9.6px;line-height:1.26;color:#fff;font-weight:400}
.web-pill{left:27px;top:535px;width:190px;height:45px;background:var(--lime);border-radius:12px 12px 0 0;text-align:center;padding-top:9px;font-weight:600;font-size:10.5px}

/* inside */
.header-band{left:0;top:0;width:740px;height:75px;background:linear-gradient(90deg,#2d2d2f,#48484a 45%,#3a3a3c 70%,#2d2d2f)}
.col-title{top:30px;font-weight:600;font-size:22px;color:var(--lime-bright)}
.about-bg{left:0;top:70px;width:247px;height:350px;background:var(--lime)}
.about-text{left:25px;top:82px;width:205px}
.body-copy{font-size:6.3px;line-height:1.36;text-align:justify;color:#2f2f2f;margin-bottom:7px}
.col .body-copy{line-height:1.5;margin-bottom:8px}
.bar{position:absolute;height:19px}
.bar svg{position:absolute;left:0;top:0}
.bar span{position:absolute;left:14px;top:2px;font-weight:800;font-style:italic;font-size:13px;color:var(--lime-bright);white-space:nowrap}
.sub-title{font-weight:800;font-style:italic;font-size:13px;color:var(--ink)}
.col{width:212px}
.footer-band{left:0;top:418px;width:740px;height:158px;background:var(--charcoal-deep)}
.stripe{height:2px;background:var(--lime)}
.stripe--grey{background:#bbb}
.photo-frame{top:407px;width:190px;height:120px;border:3px solid #555}
.footer-web{top:540px;width:247px;text-align:center;font-weight:600;font-size:10.5px;color:var(--lime-bright)}
</style>
</head>
<body>

<section class="sheet sheet--outside">

  <div class="panel panel--ways">
    <div class="abs top-strip"></div>

    <svg class="abs" style="left:28px;top:38px" width="58" height="46" viewBox="0 0 58 46" aria-hidden="true">
      <g fill="none" stroke="var(--gold)" stroke-width="2" stroke-linecap="round">
        <path d="M23 44V26l-5-6M23 26V8M28 24V5M33 24V7M38 26V12M23 44h15V30l4-8"/>
        <path d="M4 16h8M6 28l7-3M4 22h7M46 16h8M47 28l-7-3M47 22h7"/>
      </g>
    </svg>
    <div class="way-title" style="left:93px;top:41px">How we<b>SERVE</b></div>
    <p class="way-text" style="left:29px;top:101px;width:200px">Our mission is to raise up a generation of young people who are firmly grounded in their relationship with Jesus Christ.</p>
    <div class="divider" style="top:163px"></div>

    <svg class="abs" style="left:26px;top:176px" width="52" height="46" viewBox="0 0 52 46" aria-hidden="true">
      <path d="M26 44C8 31 1 22 1 13 1 6 7 1 14 1c5 0 9 3 12 7 3-4 7-7 12-7 7 0 13 5 13 12 0 9-7 18-25 31z" fill="var(--heart)"/>
    </svg>
    <div class="way-title" style="left:90px;top:177px">Partner<b>WITH US</b></div>
    <p class="way-text" style="left:26px;top:233px;width:204px">By partnering with Lamp over the Valleys, you are never simply a “sponsor” or “donor”;  you are changing lives in East Africa</p>
    <div class="divider" style="top:297px"></div>

    <svg class="abs" style="left:30px;top:313px" width="44" height="58" viewBox="0 0 44 58" aria-hidden="true">
      <rect x="2" y="2" width="40" height="54" rx="3" fill="var(--book)"/>
      <rect x="36" y="4" width="5" height="50" fill="#e8f7fd"/>
      <path d="M8 2h5v12l-2.5-2-2.5 2z" fill="#f2c230"/>
    </svg>
    <div class="way-title" style="left:90px;top:309px;font-weight:600;font-size:19px;line-height:1.1">Are you a<br>BIBLE<br>TEACHER?</div>
    <p class="way-text" style="left:26px;top:386px;width:200px">We depend on visiting pastors / Bible teachers.  Come make an impact on students who hunger to learn God’s word.</p>

    <div class="abs photo-field" role="img" aria-label="Photo of open grassland under a misty sky"></div>
  </div>

  <div class="panel panel--mission">
    <div class="abs photo-faded" role="img" aria-label="Faded photo of a smiling child, tinted green"></div>
    <h2 class="abs mission-head">TO BRING<br>LIGHT TO THE<br>VALLEYS</h2>
    <p class="abs mission-sub">through the knowledge<br>of Jesus Christ and<br>the Word of God.</p>
    <p class="abs verse">Matt. 12:21</p>
    <p class="abs org-name">Lamp Over The Valleys</p>
    <p class="abs contact" style="top:461px">PO Box 4410<br>Cedarford, CA 95000</p>
    <p class="abs contact" style="top:502px">info@lampoverthevalleystz.example</p>
    <p class="abs contact" style="top:529px">www.lampoverthevalleystz.example</p>
  </div>

  <div class="panel panel--cover">
    <p class="abs org-wordmark">LAMP OVER<br>THE VALLEYS</p>
    <h1 class="abs thanks">THANK YOU!</h1>
    <p class="abs thanks-sub">FOR CONSIDERING THIS<br>PROJECT</p>
    <svg class="abs" style="left:110px;top:168px" width="137" height="53" viewBox="0 0 137 53" aria-hidden="true">
      <path d="M137 1H108c-10 0-10 20-22 20H40c-8 0-8 12-14 12" fill="none" stroke="var(--lime-bright)" stroke-width="2"/>
    </svg>
    <div class="abs photo-kids" role="img" aria-label="Photo of schoolchildren in checked uniforms, one with hands folded in prayer"></div>
    <div class="abs" style="left:0;top:221px;width:247px;height:3px;background:var(--lime-bright)"></div>
    <p class="abs cover-text">Your efforts help in educating and feeding 225 street children, providing a safe haven and trade school for hundreds of women and abused teenagers, medical ship on the longest lake in the world going into unreached people groups, a Bible College Training up pastors to plant churches all over TZ, Congo, Burundi and beyond, youth and children’s kids clubs and youth camps.</p>
    <div class="abs web-pill">www.lampoverthevalleystz.example</div>
  </div>
</section>

<section class="sheet sheet--inside">
  <div class="abs header-band" role="img" aria-label="Dark photo of a crowd of young people at an outreach"></div>
  <h2 class="abs col-title" style="left:26px">About Us</h2>
  <h2 class="abs col-title" style="left:266px">How We Serve</h2>
  <h2 class="abs col-title" style="left:506px">How We Serve</h2>

  <div class="abs about-bg"></div>
  <div class="abs" style="left:247px;top:75px;width:246px;height:343px;background:linear-gradient(90deg,#fff 85%,#eee)"></div>
  <svg class="abs" style="left:493px;top:70px" width="247" height="26" viewBox="0 0 247 26" aria-hidden="true">
    <path d="M0 5h125c8 0 8 20 18 20h104v1H0z" fill="var(--paper)"/>
    <path d="M0 5h125c8 0 8 20 18 20h104" fill="none" stroke="var(--lime)" stroke-width="4"/>
  </svg>

  <div class="abs about-text">
    <p class="body-copy">Lamp over the Valleys (LotV) has its headquarters in Kigoma, Tanzania, on the longest lake in the world – Lake Tanganyika. It is also the second deepest lake in the world, at close to a mile deep. Over 2 million people live around its shores. Four different countries – Congo, Zambia, Burundi, and Tanzania – have their borders in the lake. Kigoma is a strategic port city. Goods are sent by train from Tanzania’s eastern seaport to Kigoma’s port and loaded on ships to reach the land-locked countries surrounding the lake.</p>
    <p class="body-copy">Walter and Ruth Engstrom founded Lamp over the Valleys in 2007, but the non-profit has grown much more substantial than just the two of them. Today LotV has six nationals on the missionary staff and employs 45 other locals who help carry on the ministry. Our objective is to raise up nationals who see Jesus as the primary need in this and every nation. Our goal is to make disciples — that’s what Jesus told us to do in Matthew 28:19-20. Ultimately that is the only hope any nation has. Our mission is: “To bring light to the valleys through the knowledge of Jesus Christ and the Word of God.” (Matt. 12:21)</p>
    <p class="body-copy">How do you bring hope to a region? There are so many things that can and need to be done in Kigoma, one of the poorest regions in Tanzania. However, we believe it starts with education — and not just a secular education, though that is necessary. The only way to bring hope and affect change in the whole land is to teach people about Jesus. We approach that goal in many different ways. One is to raise up a new generation that will become godly influencers. There is also a need to educate pastors. Those who are responsible for equipping the Church for the work of the ministry. Starting at each end of the spectrum became our heart’s desire.</p>
    <p class="body-copy">Through LotV, the hope that is found in Jesus Christ is starting to infiltrate this country and its neighbors.</p>
  </div>

  <div class="bar" style="left:253px;top:88px;width:181px">
    <svg width="181" height="19" aria-hidden="true"><path d="M0 0h181l-10 19H0z" fill="var(--charcoal)"/></svg>
    <span>EDUCATION</span>
  </div>
  <div class="abs col" style="left:269px;top:115px">
    <p class="body-copy">Our vision is to raise up a generation of godly influencers. These are young people who are firmly grounded in their relationship with Jesus Christ. They have received the best education, enabling them to take up positions of influence in every area of their country. We started with a preschool, which over the years grew into a primary school with over 200 students.</p>
    <p class="body-copy">At the other end of the spectrum, we felt a call to equip the current leaders of the local churches by forming a Bible College.</p>
    <p class="body-copy">Only around 5% of pastors in our region had received any Bible training whatsoever.</p>
    <p class="body-copy">Today pastors are being trained in the Word of God – how to study and how to teach. Many of our grads have gone on to plant churches and start other ministries that serve their communities.</p>
  </div>
  <div class="bar" style="left:253px;top:266px;width:181px">
    <svg width="181" height="19" aria-hidden="true"><path d="M0 0h181l-10 19H0z" fill="var(--charcoal)"/></svg>
    <span>VILLAGE OUTREACHES</span>
  </div>
  <div class="abs col" style="left:269px;top:293px">
    <p class="body-copy">Our village outreaches are an exciting time to bring help and hope to remote villages along Lake Tanganyika. We have seen much fruit from these outreaches over the years.</p>
    <p class="body-copy">The outreach can consist of many different parts, such as seeking out candidates for the Bible College. Setting up new Kid’s Clubs, a variety of medical training and services, seminars, Jesus film at night, and door-to-door evangelism are also a part of our outreach.</p>
    <p class="body-copy">We happily host teams from North America who feel the call to join us in outreach.</p>
  </div>

  <p class="abs sub-title" style="left:508px;top:90px">KID’S CLUBS</p>
  <div class="abs col" style="left:508px;top:115px">
    <p class="body-copy">Kid’s Clubs started as an outreach to children who survive on the streets. During the 2 hour weekly gatherings, the children receive food, play games, and learn everything from the most basic hygiene practices to the most-essential Word of God.</p>
    <p class="body-copy">This ministry has grown from 19 kids and 5 leaders in the first week, to over 1000 kids and more than 70 leaders in 14 different locations from Kigoma to almost 100 miles south on Lake Tanganyika.</p>
    <p class="body-copy">We hold annual summer camps for youth to refresh and recruit new leaders to the program. We also hold Kid’s camps to teach and encourage those children who have been a part of Kid’s Clubs during the year.</p>
  </div>
  <div class="bar" style="left:495px;top:266px;width:182px">
    <svg width="182" height="19" aria-hidden="true"><path d="M0 0h182l-10 19H0z" fill="var(--charcoal)"/></svg>
    <span>MICRO-BUSINESSES</span>
  </div>
  <div class="abs col" style="left:508px;top:293px">
    <p class="body-copy">Jobs are hard to come by. However, through our Vocational Training Center, men and women are given the skills needed to help them support their families.</p>
    <p class="body-copy">Training has included sewing, jewelry making, bread baking, welding, concrete finishing, and business skills. If you have a trade to teach, we would love to host you.</p>
    <p class="body-copy">We have also been able to grant Micro-Business Loans to get our grads started in their own business.</p>
  </div>

  <div class="abs footer-band" role="img" aria-label="Dark faded photo of a classroom"></div>
  <div class="abs" style="left:0;top:424px;width:740px">
    <div class="stripe" style="margin-bottom:3px"></div>
    <div class="stripe stripe--grey"></div>
  </div>
  <div class="abs photo-frame" style="left:34px;background:linear-gradient(135deg,#c9c3b8,#6f5a48 45%,#3a2d26 80%)" role="img" aria-label="Photo of students with headphones working on laptops"></div>
  <div class="abs photo-frame" style="left:276px;background:linear-gradient(135deg,#c7a57c,#8a5a3c 40%,#d26a3a 65%,#4a3a32)" role="img" aria-label="Photo of women at sewing machines in a training workshop"></div>
  <div class="abs photo-frame" style="left:515px;background:linear-gradient(135deg,#8b7a6a,#5a4838 40%,#8fa8a0 65%,#3b302a)" role="img" aria-label="Photo of smiling children gathered in a classroom"></div>
  <p class="abs footer-web" style="left:0">www.lampoverthevalleystz.example</p>
  <p class="abs footer-web" style="left:247px">www.lampoverthevalleystz.example</p>
  <p class="abs footer-web" style="left:493px">www.lampoverthevalleystz.example</p>
</section>

</body>
</html>
```